Brightwell Aero Services Logo

I need a website and logo for the parent company Brightwell Aero Services, which encompasses general aviation aircraft repair, small aircrat rental and flight school. The company is based in Lawrenceville, Georgia at the Tolleson county airport. A saying that can be incorporated somehere could be, "Quality flying is safe flying", "Safety in mind is no accident" ,. I need a website and logo.

The company started as a repair shop performing repairs and inspections on Harlan, Vantor, Delkin and Ralstead general aviation aircraft, all models of single engine piston, multi engine piston, and single engine turboprop with an emphasis on Harlan Solvane and AeroTurn turbo prop aircraft. We have se=ince entered the aircraft rental and flight instruction market using the Delkin 240 ang Harlan Ranger aircraft.

Number of Pages; I don't know. Maybe 5 ? A home page for Brightwell Aero Services, page for maintenance and repairs and a couple for the rental and school. The maintenance shop is busy, always has been. I need to get the rental and school advertised and busy.

I have a logo for the maintenance shop shirts, not for the school. I do not have the file. I paid a business locally to do that and print on the shirts. They have the file.

Target Market(s)

In our flight school rental fleet department, we are looking for persons wishing to obtain their private pilot license and continuing on into their commercial and instrument ratings. In the aircraft maintenance department, we are looking for new customers who want a better and more quality relationship with their aircraft maintenance provider who will give more detail and quality in the repairs with an emphasis on safety and fewer problems between scheduled maintenance cycles on their aircraft. Brightwell's owner, Dale Hutchins, has been performing aircraft maintenance in the Atlanta area for 27 years. He has built a steady customer base through those years.

```html
<!DOCTYPE html>
<html lang="en">
<head>
<meta charset="utf-8">
<title>Brightwell Aero</title>
<link href="https://fonts.googleapis.com/css2?family=Roboto:wght@400;500;700&display=swap" rel="stylesheet">
<style>
:root{
  --navy:#063a6b;
  --navy-deep:#032b52;
  --ink:#222;
  --muted:#444;
  --white:#fff;
  --footer:#2b2f38;
  --card-active:#e4e9ee;
}
*{box-sizing:border-box;margin:0;padding:0}
html,body{width:1200px;height:4691px;overflow:hidden}
body{position:relative;font-family:"Roboto",Arial,sans-serif;color:var(--ink);background:var(--white)}
.abs{position:absolute}
a{color:inherit;text-decoration:none}

/* header */
.topbar{left:474px;top:0;width:726px;height:40px;background:var(--navy);color:var(--white);font-size:15px;display:flex;align-items:center;padding-left:52px;gap:40px}
.topbar .item{display:flex;align-items:center;gap:10px;white-space:nowrap}
.social{display:flex;gap:10px;margin-left:26px}
.social span{width:25px;height:25px;border-radius:50%;background:var(--white);display:block}
.brand{left:100px;top:8px;display:flex;align-items:center;gap:12px;color:var(--navy);font-size:27px;font-weight:500;white-space:nowrap}
.brand .mark{width:44px;height:44px;border-radius:50%;border:3px solid var(--navy)}
.nav{left:588px;top:50px;display:flex;gap:36px;font-size:15px;color:var(--ink);align-items:center;white-space:nowrap}
.nav .active{color:var(--navy);font-weight:700;text-decoration:underline;text-underline-offset:6px}

/* hero */
.hero{left:0;top:80px;width:1200px;height:600px;background:linear-gradient(135deg,#5b5f63 0%,#8b8d8a 35%,#b8b4a8 55%,#6d6f70 80%,#3f4245 100%)}
.hero-box{left:188px;top:262px;width:823px;height:200px;background:rgba(40,45,55,.35)}
.hero-title{left:0;top:308px;width:1200px;text-align:center;color:var(--white);font-weight:700;font-size:53px;line-height:62px;text-shadow:0 3px 8px rgba(0,0,0,.55)}
.arrow{width:30px;height:30px;border-radius:50%;background:rgba(255,255,255,.9);display:flex;align-items:center;justify-content:center}
.hero-curve{left:0;top:520px}

/* generic */
h2{font-weight:500;font-size:33px;color:var(--navy);white-space:nowrap}
.para{font-size:14.5px;line-height:31px;color:var(--muted)}
.btn{display:flex;align-items:center;justify-content:center;border-radius:24px;font-weight:700;font-size:16px}
.btn-navy{background:var(--navy);color:var(--white)}
.btn-white{background:var(--white);color:var(--navy)}

/* about */
.about-title{left:98px;top:747px}
.about-text{left:98px;top:792px;width:510px}
.about-btn{left:98px;top:1149px;width:137px;height:49px}
.about-visual{left:640px;top:728px}

/* services */
.services{left:0;top:1297px;width:1200px;height:670px;background:linear-gradient(160deg,#0c4b84 0%,#063a6b 45%,#032b52 100%)}
.services-title{left:0;top:1347px;width:1200px;text-align:center;color:var(--white)}
.card{background:var(--white);width:326px;border-radius:3px;box-shadow:0 4px 14px rgba(0,0,0,.2);text-align:center}
.card.active{background:var(--card-active)}
.card .photo{height:208px;width:100%}
.card .icon{width:60px;height:60px;border-radius:50%;background:var(--navy);margin:-32px auto 0;position:relative;display:flex;align-items:center;justify-content:center;border:3px solid var(--white)}
.card.active .icon{background:var(--white);border-color:#dde3ea}
.card h3{font-size:21px;font-weight:500;color:var(--navy);margin-top:6px}
.card.active h3{color:var(--ink)}
.card p{font-size:14.5px;line-height:31px;color:var(--muted);padding:2px 22px 0}
.card .more{display:inline-block;margin:2px 0 22px;font-weight:700;font-size:16px;color:var(--navy);text-decoration:underline;text-underline-offset:3px}

/* gallery */
.gallery-title{left:0;top:2030px;width:1200px;text-align:center}
.shot{border-radius:3px}

/* rental */
.rental{left:0;top:2877px;width:1200px;height:565px;background:var(--navy)}
.rental-title{left:95px;top:2940px;color:var(--white)}
.rental-text{left:97px;top:2985px;width:525px;color:#e8eef5}
.rental-btn{left:98px;top:3311px;width:137px;height:49px}

/* partners */
.partners-title{left:0;top:3496px;width:1200px;text-align:center}
.partner{width:178px;height:171px;background:var(--white);box-shadow:0 3px 14px rgba(0,0,0,.14);display:flex;align-items:center;justify-content:center;font-size:34px;font-weight:700;color:var(--navy)}
.partner.active{border-bottom:5px solid var(--navy)}

/* contact */
.contact-title{left:98px;top:3870px}
.contact-item{left:98px;width:400px;display:flex;gap:24px;align-items:flex-start}
.contact-item .ico{width:70px;height:70px;border-radius:50%;background:var(--navy);display:flex;align-items:center;justify-content:center;flex:none}
.contact-item .lbl{font-size:20px;font-weight:700;color:var(--navy);margin-top:4px}
.contact-item .val{font-size:20px;color:var(--ink);margin-top:8px;white-space:nowrap}
.form{left:521px;top:3815px;width:581px;height:474px;background:var(--navy);border-radius:12px}
.form-title{left:568px;top:3852px;color:var(--white);font-size:30px;font-weight:700}
.field{left:568px;width:486px;border:1px solid rgba(255,255,255,.85);color:var(--white);font-size:14px;padding:14px 16px}
.send{left:568px;top:4197px;width:129px;height:48px;font-size:20px}

/* footer */
.footer{left:0;top:4361px;width:1200px;height:330px;background:var(--footer);color:var(--white)}
.footer-brand{left:0;top:4438px;width:1200px;display:flex;justify-content:center;align-items:center;gap:14px;font-size:27px;font-weight:500;color:var(--white)}
.footer-brand .mark{width:48px;height:48px;border-radius:50%;border:3px solid var(--white)}
.footer-links{left:0;top:4540px;width:1200px;display:flex;justify-content:center;gap:34px;font-size:15px;color:var(--white)}
.copyright{left:0;top:4603px;width:1200px;text-align:center;font-size:14.5px;color:var(--white)}
</style>
</head>
<body>

<!-- header -->
<div class="abs topbar">
  <div class="item">
    <svg width="16" height="16" viewBox="0 0 24 24"><path fill="#fff" d="M6.6 10.8a15.1 15.1 0 0 0 6.6 6.6l2.2-2.2c.3-.3.7-.4 1-.2 1.1.4 2.3.6 3.6.6.6 0 1 .4 1 1V20c0 .6-.4 1-1 1A17 17 0 0 1 3 4c0-.6.4-1 1-1h3.5c.6 0 1 .4 1 1 0 1.3.2 2.5.6 3.6.1.3 0 .7-.2 1z"/></svg>
    +1 555 0142 0199
  </div>
  <div class="item">
    <svg width="20" height="15" viewBox="0 0 24 18"><path fill="#fff" d="M0 0h24v18H0z"/><path fill="none" stroke="#063a6b" stroke-width="2" d="M1 1l11 8 11-8"/></svg>
    info@brightwellaero.example
  </div>
  <div class="social" aria-label="Social links"><span></span><span></span><span></span><span></span></div>
</div>

<div class="abs brand"><span class="mark"></span>Brightwell Aero</div>

<nav class="abs nav">
  <a class="active">Home</a><a>About Us</a><a>Services</a><a>School &amp; Rental</a><a>Contact</a>
  <svg width="20" height="20" viewBox="0 0 24 24"><circle cx="10" cy="10" r="7" fill="none" stroke="#222" stroke-width="2.4"/><path d="M15 15l7 7" stroke="#222" stroke-width="2.4"/></svg>
</nav>

<!-- hero -->
<div class="abs hero" role="img" aria-label="Small aircraft undergoing maintenance inside a hangar"></div>
<div class="abs hero-box"></div>
<h1 class="abs hero-title">Quality flying is safe flying<br>Safety in mind is no accident</h1>
<div class="abs arrow" style="left:1116px;top:366px"><svg width="12" height="12" viewBox="0 0 12 12"><path d="M4 2l4 4-4 4" fill="none" stroke="#222" stroke-width="2"/></svg></div>
<svg class="abs hero-curve" width="1200" height="170" viewBox="0 0 1200 170">
  <path d="M0 30 Q600 240 1200 42 L1200 170 L0 170 Z" fill="#fff"/>
  <path d="M0 30 Q600 240 1200 42 Q600 200 0 30 Z" fill="#10151c"/>
</svg>

<!-- about -->
<h2 class="abs about-title">About Us</h2>
<p class="abs para about-text">Sed ut perspiciatis unde omnis iste natus error sit voluptatem accusantium doloremque laudantium, totam rem aperiam, eaque ipsa quae ab illo inventore veritatis et quasi architecto beatae vitae dicta sunt explicabo. Nemo enim ipsam voluptatem quia voluptas sit aspernatur aut odit aut fugit, sed quia consequuntur magni dolores eos qui ratione voluptatem sequi nesciunt. Neque porro quisquam est, qui dolorem ipsum quia dolor sit amet, consectetur, adipisci velit, sed quia non numquam eius modi tempora incidunt ut labore et dolore magnam aliquam quaerat voluptatem. Ut enim ad minima veniam, quis nostrum exercitationem ullam corporis suscipit laboriosam, nisi ut aliquid ex ea commodi consequatur?</p>
<a class="abs btn btn-navy about-btn">Read More</a>
<svg class="abs about-visual" width="470" height="500" viewBox="0 0 470 500">
  <circle cx="235" cy="244" r="216" fill="none" stroke="#063a6b" stroke-width="2.5"/>
  <circle cx="225" cy="262" r="218" fill="#063a6b"/>
  <circle cx="240" cy="245" r="214" fill="#fff"/>
  <defs><linearGradient id="hangar" x1="0" y1="0" x2="0" y2="1"><stop offset="0" stop-color="#6e6a63"/><stop offset=".55" stop-color="#a7a59f"/><stop offset="1" stop-color="#4d4f52"/></linearGradient></defs>
  <circle cx="240" cy="245" r="212" fill="url(#hangar)" role="img" aria-label="White single-engine aircraft parked in a hangar"/>
</svg>

<!-- services -->
<div class="abs services" role="img" aria-label="Blue sky with aircraft background"></div>
<h2 class="abs services-title">Our Services</h2>

<div class="abs card" style="left:98px;top:1422px;height:435px">
  <div class="photo" style="background:linear-gradient(135deg,#4b5560,#8a7d74 50%,#7a2a2a)" role="img" aria-label="Mechanics repairing an aircraft engine"></div>
  <div class="icon"><svg width="30" height="26" viewBox="0 0 30 26"><path d="M2 12L15 3l13 9v12H2z" fill="none" stroke="#fff" stroke-width="2"/><rect x="8" y="13" width="14" height="11" fill="none" stroke="#fff" stroke-width="2"/></svg></div>
  <h3>Aircraft Repair</h3>
  <p>Lorem ipsum dolor sit amet, consectetur adipiscing elit, sed do eiusmod tempor incididunt ut labore et dolore magna</p>
  <a class="more">View More</a>
</div>

<div class="abs card active" style="left:439px;top:1439px;height:446px">
  <div class="photo" style="background:linear-gradient(180deg,#9bb4c8 0%,#d9a86a 45%,#6f5a44 100%)" role="img" aria-label="Small jet taxiing on a runway at sunset"></div>
  <div class="icon"><svg width="32" height="22" viewBox="0 0 32 22"><path d="M2 12h28M8 7l8 5-8 5M20 4l4 8-4 8" fill="none" stroke="#063a6b" stroke-width="2"/></svg></div>
  <h3>Small Aircraft Rental</h3>
  <p>Lorem ipsum dolor sit amet, consectetur adipiscing elit, sed do eiusmod tempor incididunt ut labore et dolore magna</p>
  <a class="more">View More</a>
</div>

<div class="abs card" style="left:778px;top:1422px;height:435px">
  <div class="photo" style="background:linear-gradient(180deg,#7fa07a 0%,#c8ccd0 40%,#4d5358 100%)" role="img" aria-label="Instructor and student pilot in a flight simulator"></div>
  <div class="icon"><svg width="28" height="28" viewBox="0 0 28 28"><path d="M4 24L24 4M10 8l10 10M6 16l6 6M16 4l8 8" fill="none" stroke="#fff" stroke-width="2"/></svg></div>
  <h3>Flight School</h3>
  <p>Lorem ipsum dolor sit amet, consectetur adipiscing elit, sed do eiusmod tempor incididunt ut labore et dolore magna</p>
  <a class="more">View More</a>
</div>

<!-- gallery -->
<h2 class="abs gallery-title"><span style="color:var(--navy)">Our</span> <span style="color:var(--ink)">Gallery</span></h2>
<div class="abs shot" style="left:98px;top:2083px;width:485px;height:354px;background:linear-gradient(180deg,#4f88c9 0%,#8fb7dc 40%,#3d6a3a 55%,#4a4a48 75%,#2f2f2f 100%)" role="img" aria-label="Low-wing aircraft parked on a tarmac"></div>
<div class="abs shot" style="left:590px;top:2083px;width:484px;height:354px;background:linear-gradient(180deg,#aeb7a8 0%,#5b6a4c 40%,#8b8f80 70%,#6d6a5a 100%)" role="img" aria-label="Training aircraft taking off from a grass field"></div>
<div class="abs shot" style="left:126px;top:2444px;width:484px;height:355px;background:linear-gradient(180deg,#4d79a6 0%,#a8c0d6 45%,#9c9d97 70%,#5f5f5c 100%)" role="img" aria-label="High-wing aircraft on a runway with yellow centre line"></div>
<div class="abs shot" style="left:617px;top:2444px;width:485px;height:355px;background:linear-gradient(160deg,#3b3a44 0%,#b25a32 45%,#e9923b 60%,#1d1a1c 100%)" role="img" aria-label="Aircraft silhouetted against a sunset"></div>

<!-- rental & school -->
<div class="abs rental"></div>
<h2 class="abs rental-title">Rental and School Aviation</h2>
<p class="abs para rental-text">Sed ut perspiciatis unde omnis iste natus error sit voluptatem accusantium doloremque laudantium, totam rem aperiam, eaque ipsa quae ab illo inventore veritatis et quasi architecto beatae vitae dicta sunt explicabo. Nemo enim ipsam voluptatem quia voluptas sit aspernatur aut odit aut fugit, sed quia consequuntur magni dolores eos qui ratione voluptatem sequi nesciunt. Neque porro quisquam est, qui dolorem ipsum quia dolor sit amet, consectetur, adipisci velit, sed quia non numquam eius modi tempora incidunt ut labore et dolore magnam aliquam quaerat voluptatem. Ut enim ad minima veniam, quis nostrum exercitationem ullam corporis suscipit laboriosam, nisi ut aliquid ex ea commodi consequatur.</p>
<a class="abs btn btn-white rental-btn">Read More</a>
<svg class="abs" style="left:648px;top:2928px" width="452" height="452" viewBox="0 0 452 452">
  <circle cx="226" cy="226" r="222" fill="#5f7fa3"/>
  <defs><linearGradient id="dusk" x1="0" y1="0" x2="0" y2="1"><stop offset="0" stop-color="#e9c4a4"/><stop offset=".6" stop-color="#d6a98a"/><stop offset="1" stop-color="#5a5048"/></linearGradient></defs>
  <circle cx="226" cy="226" r="214" fill="url(#dusk)" role="img" aria-label="Two light aircraft, one landing at dusk"/>
</svg>

<!-- partners -->
<h2 class="abs partners-title"><span style="color:var(--navy)">Our</span> <span style="color:var(--ink)">Partners</span></h2>
<div class="abs partner" style="left:180px;top:3566px">Harlan</div>
<div class="abs partner" style="left:401px;top:3566px">Delkin</div>
<div class="abs partner active" style="left:621px;top:3566px">Ralstead</div>
<div class="abs partner" style="left:841px;top:3566px">Vantor</div>

<!-- contact -->
<h2 class="abs contact-title">Contact Us</h2>
<div class="abs contact-item" style="top:3935px">
  <div class="ico"><svg width="24" height="24" viewBox="0 0 24 24"><path fill="#fff" d="M6.6 10.8a15.1 15.1 0 0 0 6.6 6.6l2.2-2.2c.3-.3.7-.4 1-.2 1.1.4 2.3.6 3.6.6.6 0 1 .4 1 1V20c0 .6-.4 1-1 1A17 17 0 0 1 3 4c0-.6.4-1 1-1h3.5c.6 0 1 .4 1 1 0 1.3.2 2.5.6 3.6.1.3 0 .7-.2 1z"/></svg></div>
  <div><div class="lbl">Phone :</div><div class="val">+1 555 0142 0199</div></div>
</div>
<div class="abs contact-item" style="top:4047px">
  <div class="ico"><svg width="26" height="19" viewBox="0 0 24 18"><path fill="#fff" d="M0 0h24v18H0z"/><path fill="none" stroke="#063a6b" stroke-width="2" d="M1 1l11 8 11-8"/></svg></div>
  <div><div class="lbl">Email :</div><div class="val">info@brightwellaero.example</div></div>
</div>
<div class="abs contact-item" style="top:4158px">
  <div class="ico"><svg width="20" height="26" viewBox="0 0 20 26"><path fill="#fff" d="M10 0a10 10 0 0 0-10 10c0 7 10 16 10 16s10-9 10-16A10 10 0 0 0 10 0z"/><circle cx="10" cy="10" r="3.5" fill="#063a6b"/></svg></div>
  <div><div class="lbl">Location :</div><div class="val">Brightwell Aero,Georgia.</div></div>
</div>

<div class="abs form"></div>
<div class="abs form-title">Get In Touch :</div>
<div class="abs field" style="top:3904px;height:52px">Enter Name :</div>
<div class="abs field" style="top:3970px;height:51px">Enter Email :</div>
<div class="abs field" style="top:4032px;height:51px">Enter Phone :</div>
<div class="abs field" style="top:4096px;height:82px">Message :</div>
<a class="abs btn btn-white send">Send</a>

<!-- footer -->
<footer class="abs footer"></footer>
<div class="abs footer-brand"><span class="mark"></span>Brightwell Aero</div>
<div class="abs footer-links"><a>Home</a><a>About Us</a><a>Services</a><a>Contact Us</a><a>Privacy Policy</a><a>Terms and Conditions</a></div>
<div class="abs copyright">Copyrights@2023. Brightwell Aero.All Rights Reserved</div>

</body>
</html>
```